KLV Plant Services

We are a heavy diesel mechanical business with additional air con certificates, remapping engine rebuilt

Contact Information for Business Card

Company Name, Director Name, Managing Director, Contact details, email and website

Font styles to use
Serif
Script

```html
<!DOCTYPE html>
<html lang="en">
<head>
<meta charset="utf-8">
<title>KLV Plant Services – Business Card</title>
<link href="https://fonts.googleapis.com/css2?family=Montserrat:wght@700&family=Poppins:wght@300;400&display=swap" rel="stylesheet">
<style>
  :root {
    --page-bg: #2e2e30;
    --card-white: #ffffff;
    --card-black: #141415;
    --pattern-dark: #1f1f21;
    --navy: #1a1a7a;
    --ink: #111111;
  }
  * { box-sizing: border-box; margin: 0; padding: 0; }
  html, body { width: 1200px; height: 881px; overflow: hidden; }
  body {
    background: var(--page-bg);
    position: relative;
    font-family: "Poppins", sans-serif;
  }
  .card {
    position: absolute;
    left: 260px;
    width: 680px;
    height: 388px;
    border-radius: 28px;
    border-bottom: 5px solid var(--navy);
    overflow: hidden;
  }
  .card-back { top: 34px; background: var(--card-black); }
  .back-pattern {
    position: absolute; inset: 0;
    background: radial-gradient(circle at 50% 45%, var(--pattern-dark), var(--card-black) 75%);
  }
  .card-front { top: 458px; background: var(--card-white); color: var(--ink); }

  .website {
    position: absolute; right: 50px; top: 58px;
    font-size: 16px; letter-spacing: 2.5px; font-weight: 400;
  }
  .website .domain { color: var(--navy); }
  .name {
    position: absolute; left: 50px; top: 76px;
    font-family: "Montserrat", sans-serif; font-weight: 700;
    font-size: 27px; letter-spacing: 1px; color: var(--navy);
  }
  .role {
    position: absolute; left: 50px; top: 112px;
    font-size: 17px; font-weight: 300;
  }
  .rule {
    position: absolute; left: 50px; right: 50px; top: 142px;
    height: 1.5px; background: var(--navy);
  }
  .address {
    position: absolute; left: 70px; top: 196px;
    font-size: 17px; font-weight: 300; line-height: 1.35; letter-spacing: 0.5px;
  }
  .contact {
    position: absolute; left: 70px; top: 282px;
    list-style: none; font-size: 19px; font-weight: 300; letter-spacing: 0.6px;
  }
  .contact li { display: flex; align-items: center; gap: 10px; line-height: 1.35; }
  .contact svg { width: 16px; height: 16px; flex: none; }

  .brand {
    position: absolute; right: 50px; top: 212px;
    display: flex; align-items: center; gap: 10px;
  }
  .brand-dot {
    width: 26px; height: 26px; border-radius: 50%;
    background: var(--navy); flex: none;
  }
  .brand-name {
    font-family: "Montserrat", sans-serif; font-weight: 700;
    font-size: 22px; letter-spacing: 0.5px; color: var(--navy);
    white-space: nowrap;
  }
</style>
</head>
<body>
  <section class="card card-back">
    <div class="back-pattern" role="img" aria-label="Repeating pattern of the company mark in glossy black on black"></div>
  </section>

  <section class="card card-front">
    <p class="website">www.<span class="domain">klvplantservices.com</span></p>
    <h1 class="name">MARK ELLISON</h1>
    <p class="role">Director</p>
    <div class="rule"></div>

    <p class="address">1270 Ridgeway Ave Norcross<br>Park, GA 30099</p>

    <ul class="contact">
      <li>
        <svg viewBox="0 0 16 16" aria-hidden="true"><path d="M4 1.5 6 4.5 4.8 6c.8 2 2.4 3.7 4.4 4.6L10.6 9.4l3 2-1 2.6C7 13.5 2.5 9 2 3.4z" fill="var(--navy)"/></svg>
        470-555-0182
      </li>
      <li>
        <svg viewBox="0 0 16 16" aria-hidden="true"><rect x="1.5" y="3.5" width="13" height="9" rx="1.5" fill="none" stroke="var(--navy)" stroke-width="1.5"/><path d="M2 4.5 8 9l6-4.5" fill="none" stroke="var(--navy)" stroke-width="1.5"/></svg>
        info@klvplantservices.com
      </li>
    </ul>

    <div class="brand">
      <span class="brand-dot" aria-hidden="true"></span>
      <span class="brand-name">KLV Plant Services</span>
    </div>
  </section>
</body>
</html>
```